Kids with Autism Clinic Goal tracking

Looking for a cute, but functional design for a large poster to put in our office that has 160 images/icons of a kid that can get colored in as we grow our clinic with more kids. So as we add kids, we color them in on the chart. And the kids border colors can change as we get closer to the goal., and somewhere on their to keep the running total.. There should be milestones at 60 kids, 80 kids, 100 kids, etc. until 160 (and the count should be accurate). Also can create stickers of kids to put into the tracker. Should be in Landscapce mode.

Designs look the same

Went on vacation/holiday

Child Mental Health Therapy

• Landscape Mode.

```html
<!DOCTYPE html>
<html lang="en">
<head>
<meta charset="utf-8">
<title>2026 Goal Tracker</title>
<link rel="stylesheet" href="https://fonts.googleapis.com/css2?family=Poppins:wght@200;600;700&display=swap">
<style>
  :root {
    --paper: #f4f3f2;
    --red: #e5505e;
    --teal: #3e6a78;
    --yellow: #f2c45a;
    --ink: #1c1c1c;
    --panel: #f0e2dd;
    --field: #ececec;
    --row-1: #f5e3c0;
    --row-2: #f3d3c8;
    --row-3: #ecb49f;
    --row-4: #f3d7d3;
    --row-5: #f3d6d8;
    --row-6: #f1d0d4;
    --row-7: #eeb8bf;
    --row-8: #e97c87;
  }
  html, body { margin: 0; padding: 0; overflow: hidden; background: var(--paper); }
  .poster {
    position: relative; width: 1200px; height: 999px; overflow: hidden;
    background: var(--paper); font-family: "Poppins", sans-serif;
  }
  .corner { position: absolute; top: 0; }
  .corner-left { left: 0; }
  .corner-right { right: 0; }
  .title-year {
    position: absolute; left: 72px; top: 78px; margin: 0;
    font-size: 136px; font-weight: 700; line-height: 1; color: var(--red); letter-spacing: -2px;
  }
  .title-words {
    position: absolute; left: 408px; top: 100px; margin: 0;
    font-size: 62px; font-weight: 700; line-height: 0.86; color: var(--teal); letter-spacing: -0.5px;
  }
  .scoreboard {
    position: absolute; left: 762px; top: 92px; width: 369px; height: 122px;
    background: var(--panel); border-radius: 14px;
  }
  .score-label {
    position: absolute; top: 10px; margin: 0; font-size: 19px; font-weight: 600;
    color: var(--teal); letter-spacing: -0.4px;
  }
  .label-target { left: 28px; }
  .label-count { left: 190px; }
  .target-value {
    position: absolute; left: 26px; top: 36px; margin: 0;
    font-size: 66px; font-weight: 200; line-height: 1.1; color: var(--red);
  }
  .count-field {
    position: absolute; left: 188px; top: 54px; width: 156px; height: 48px;
    background: var(--field); border-radius: 6px;
  }
  .tracker-grid { position: absolute; left: 0; top: 0; }
  .meadow {
    position: absolute; left: 0; bottom: 0; width: 1200px; height: 212px;
    background: linear-gradient(180deg, rgba(244,243,242,0) 0%, #f6d3d2 35%, #f3dca6 60%, #d7ead9 100%);
  }
</style>
</head>
<body>
<div class="poster">
  <svg class="corner corner-left" width="280" height="96" viewBox="0 0 280 96" aria-hidden="true">
    <path d="M0,0 H276 C270,30 240,42 205,40 C170,38 150,48 120,60 C85,74 50,70 30,82 C15,90 5,92 0,92 Z" fill="var(--yellow)"/>
    <g fill="var(--teal)">
      <circle cx="120" cy="36" r="3"/><circle cx="121" cy="47" r="3"/>
      <circle cx="134" cy="31" r="3.5"/><circle cx="136" cy="46" r="4"/>
      <circle cx="150" cy="28" r="4"/><circle cx="152" cy="42" r="3.5"/>
      <circle cx="165" cy="31" r="3"/><circle cx="168" cy="43" r="3"/>
    </g>
  </svg>
  <svg class="corner corner-right" width="156" height="112" viewBox="0 0 156 112" aria-hidden="true">
    <path d="M0,0 H156 V112 C140,110 132,90 124,70 C115,45 95,30 60,24 C30,20 10,12 0,0 Z" fill="var(--red)"/>
  </svg>

  <h1 class="title-year">2026</h1>
  <p class="title-words">Goal<br>Tracker</p>

  <div class="scoreboard">
    <p class="score-label label-target">Our Target</p>
    <p class="score-label label-count">Current Count</p>
    <p class="target-value">160</p>
    <div class="count-field"></div>
  </div>

  <svg class="tracker-grid" width="1200" height="780" viewBox="0 0 1200 780" role="img" aria-label="Grid of 160 kid icons, 20 per row in 8 rows">
    <defs>
      <symbol id="kid" viewBox="-14 -16 28 32" overflow="visible">
        <circle cx="0" cy="-10" r="4" fill="currentColor"/>
        <path d="M-8,-9 L-3,-2 H3 L8,-9" fill="none" stroke="currentColor" stroke-width="3.6" stroke-linecap="round" stroke-linejoin="round"/>
        <rect x="-4.5" y="-4" width="9" height="11" rx="2.5" fill="currentColor"/>
        <path d="M-2.2,6 V13 M2.2,6 V13" stroke="currentColor" stroke-width="3.6" stroke-linecap="round"/>
      </symbol>
      <pattern id="row-1" x="65.37" y="259" width="53.26" height="62" patternUnits="userSpaceOnUse"><circle cx="26.63" cy="31" r="23" fill="var(--row-1)"/><use href="#kid" x="12.63" y="15" width="28" height="32" style="color:#fff"/></pattern>
      <pattern id="row-2" x="65.37" y="259" width="53.26" height="62" patternUnits="userSpaceOnUse"><circle cx="26.63" cy="31" r="23" fill="var(--row-2)"/><use href="#kid" x="12.63" y="15" width="28" height="32" style="color:#fff"/></pattern>
      <pattern id="row-3" x="65.37" y="259" width="53.26" height="62" patternUnits="userSpaceOnUse"><circle cx="26.63" cy="31" r="23" fill="var(--row-3)"/><use href="#kid" x="12.63" y="15" width="28" height="32" style="color:#fff"/></pattern>
      <pattern id="row-4" x="65.37" y="259" width="53.26" height="62" patternUnits="userSpaceOnUse"><circle cx="26.63" cy="31" r="23" fill="var(--row-4)"/><use href="#kid" x="12.63" y="15" width="28" height="32" style="color:#fff"/></pattern>
      <pattern id="row-5" x="65.37" y="259" width="53.26" height="62" patternUnits="userSpaceOnUse"><circle cx="26.63" cy="31" r="23" fill="var(--row-5)"/><use href="#kid" x="12.63" y="15" width="28" height="32" style="color:#fff"/></pattern>
      <pattern id="row-6" x="65.37" y="259" width="53.26" height="62" patternUnits="userSpaceOnUse"><circle cx="26.63" cy="31" r="23" fill="var(--row-6)"/><use href="#kid" x="12.63" y="15" width="28" height="32" style="color:#fff"/></pattern>
      <pattern id="row-7" x="65.37" y="259" width="53.26" height="62" patternUnits="userSpaceOnUse"><circle cx="26.63" cy="31" r="23" fill="var(--row-7)"/><use href="#kid" x="12.63" y="15" width="28" height="32" style="color:#fff"/></pattern>
      <pattern id="row-8" x="65.37" y="259" width="53.26" height="62" patternUnits="userSpaceOnUse"><circle cx="26.63" cy="31" r="23" fill="var(--row-8)"/><use href="#kid" x="12.63" y="15" width="28" height="32" style="color:#fff"/></pattern>
    </defs>
    <g class="tracker-rows">
      <rect x="65.37" y="259" width="1065.2" height="62" fill="url(#row-1)"/>
      <rect x="65.37" y="321" width="1065.2" height="62" fill="url(#row-2)"/>
      <rect x="65.37" y="383" width="1065.2" height="62" fill="url(#row-3)"/>
      <rect x="65.37" y="445" width="1065.2" height="62" fill="url(#row-4)"/>
      <rect x="65.37" y="507" width="1065.2" height="62" fill="url(#row-5)"/>
      <rect x="65.37" y="569" width="1065.2" height="62" fill="url(#row-6)"/>
      <rect x="65.37" y="631" width="1065.2" height="62" fill="url(#row-7)"/>
      <rect x="65.37" y="693" width="1065.2" height="62" fill="url(#row-8)"/>
    </g>
    <g class="kids-enrolled">
      <use href="#kid" x="78" y="274" width="28" height="32" style="color:var(--teal)"/>
      <use href="#kid" x="131.26" y="274" width="28" height="32" style="color:var(--ink)"/>
      <use href="#kid" x="184.52" y="274" width="28" height="32" style="color:var(--red)"/>
      <use href="#kid" x="237.78" y="274" width="28" height="32" style="color:var(--ink)"/>
    </g>
  </svg>

  <div class="meadow" role="img" aria-label="Illustrated meadow of pink, red and yellow flowers on soft green hills"></div>
</div>
</body>
</html>
```